Looking for business card/letterhead/email signature

Take existing logo and create full design suite of collateral

Contact Information for Business Card

Use mock details that can be edited by us

Font styles to use
Sans Serif

```html
<!DOCTYPE html>
<html lang="en">
<head>
<meta charset="utf-8">
<title>Renwick Digital – Stationery Suite</title>
<link rel="stylesheet" href="https://fonts.googleapis.com/css2?family=Montserrat:wght@400;500;700;800&family=Roboto+Condensed:wght@400;700&display=swap">
<style>
  :root{
    --brand-blue:#0b4e92;
    --brand-blue-line:#2a67a6;
    --paper:#ffffff;
    --paper-soft:#f3f3f3;
    --backdrop:#e5e5e5;
    --ink:#3a3a3a;
    --ink-soft:#6a6a6a;
    --shadow:0 2px 5px rgba(0,0,0,.22);
  }
  *{box-sizing:border-box;margin:0;padding:0}
  html,body{width:1200px;height:796px;overflow:hidden}
  body{background:var(--backdrop);position:relative;font-family:"Montserrat",sans-serif;color:var(--ink)}
  .piece{position:absolute;box-shadow:var(--shadow);overflow:hidden}
  .wordmark{font-family:"Montserrat",sans-serif;font-weight:800;color:var(--brand-blue);letter-spacing:-.02em;line-height:1;white-space:nowrap}
  .wordmark.on-blue{color:var(--paper)}
  .icon{width:1em;height:1em;fill:currentColor;vertical-align:-.12em;margin-left:.35em}

  /* Letterhead */
  .letterhead{left:342px;top:78px;width:336px;height:472px;background:var(--paper)}
  .letterhead .wordmark{position:absolute;top:64px;left:0;width:100%;text-align:center;font-size:18px}
  .letter-greeting{position:absolute;left:30px;top:137px;font-size:8px;color:var(--ink)}
  .letter-body{position:absolute;left:30px;top:158px;width:278px;font-size:4.6px;line-height:7.1px;color:var(--ink-soft);text-align:justify}
  .letter-body p{margin-bottom:7px}
  .letter-closing{position:absolute;left:30px;top:306px;font-size:4.8px;color:var(--ink-soft)}
  .letter-signature{position:absolute;left:26px;top:326px;width:66px;height:22px;background:linear-gradient(90deg,#c9d7ea,#e3ebf5);border-radius:3px}
  .letter-footer{position:absolute;left:44px;right:0;top:440px;height:21px;background:var(--brand-blue);color:var(--paper);font-size:4.6px;line-height:7px;text-align:center;padding-top:3px}

  /* Folder */
  .folder{left:706px;top:50px;width:395px;height:501px;background:var(--brand-blue)}
  .folder-spine{position:absolute;top:0;bottom:0;width:1px;background:var(--brand-blue-line)}
  .folder .wordmark{position:absolute;left:118px;top:230px;font-size:46px}
  .folder .wordmark small{display:block;font-size:14px;letter-spacing:.22em;margin:4px 0 0 40px;font-weight:800}

  /* Business card front (small) */
  .card-front{left:157px;top:357px;width:154px;height:87px;background:var(--paper)}
  .card-front .wordmark{position:absolute;top:32px;left:0;width:100%;text-align:center;font-size:14px}
  .card-front .card-url{position:absolute;bottom:9px;width:100%;text-align:center;font-size:3.6px;letter-spacing:.12em;color:var(--ink-soft)}

  /* Business card back */
  .card-back{background:var(--brand-blue);color:var(--paper)}
  .card-back .white-side{position:absolute;left:0;top:0;bottom:0;background:var(--paper)}
  .card-back .logo-field{position:absolute;border-radius:50%;background:var(--paper)}
  .card-back .wordmark{position:absolute}
  .card-back .card-details{position:absolute;text-align:right}
  .card-name{font-family:"Roboto Condensed",sans-serif;font-weight:700}
  .card-role{font-family:"Roboto Condensed",sans-serif;font-weight:400}
  .card-details .contact{font-family:"Roboto",sans-serif;font-family:"Roboto Condensed",sans-serif}

  .card-back.large{left:42px;top:606px;width:306px;height:147px}
  .card-back.large .white-side{width:70px}
  .card-back.large .logo-field{left:-10px;top:-18px;width:184px;height:184px}
  .card-back.large .wordmark{left:26px;top:64px;font-size:25px}
  .card-back.large .card-details{right:24px;top:26px}
  .card-back.large .card-name{font-size:10px}
  .card-back.large .card-role{font-size:7px;margin-bottom:26px}
  .card-back.large .contact{font-size:7px;line-height:8.4px}
  .card-back.large .contact.address{margin-bottom:3px}

  .card-back.small{left:158px;top:461px;width:154px;height:88px}
  .card-back.small .white-side{width:34px}
  .card-back.small .logo-field{left:-6px;top:-8px;width:102px;height:102px}
  .card-back.small .wordmark{left:11px;top:38px;font-size:13px}
  .card-back.small .card-details{right:12px;top:13px}
  .card-back.small .card-name{font-size:5px}
  .card-back.small .card-role{font-size:3.6px;margin-bottom:20px}
  .card-back.small .contact{font-size:3.4px;line-height:4.8px}

  /* Envelope front */
  .envelope-front{left:369px;top:580px;width:386px;height:176px;background:var(--paper-soft)}
  .envelope-front .wordmark{position:absolute;left:22px;top:36px;font-size:22px}
  .envelope-address{position:absolute;left:22px;top:74px;font-size:4.4px;line-height:5.6px;color:var(--ink-soft)}
  .envelope-band{position:absolute;left:55px;right:0;top:154px;height:12px;background:var(--brand-blue)}

  /* Envelope back */
  .envelope-back{left:774px;top:578px;width:386px;height:176px;background:var(--paper-soft)}
  .envelope-flap{position:absolute;left:0;top:0;width:386px;height:56px}
  .envelope-back .wordmark{position:absolute;left:0;width:100%;top:22px;padding-left:90px;text-align:center;font-size:13px}
</style>
</head>
<body>

<svg width="0" height="0" style="position:absolute" aria-hidden="true">
  <defs>
    <symbol id="i-phone" viewBox="0 0 16 16"><path d="M4 1l2.5 3-1.6 1.6c.8 1.9 2.6 3.7 4.5 4.5L11 8.5l3 2.5-1.5 2.8C7 13.5 2.5 9 2.2 3.5z"/></symbol>
    <symbol id="i-mobile" viewBox="0 0 16 16"><path d="M4.5 1h7v14h-7zM6 2.5v9.5h4V2.5z"/></symbol>
    <symbol id="i-fax" viewBox="0 0 16 16"><path d="M4 2h7v4H4zM1.5 6.5h13V13h-2v-2.5h-9V13h-2zM4.5 11.5h7V15h-7z"/></symbol>
    <symbol id="i-mail" viewBox="0 0 16 16"><path d="M1 3.5h14v9H1zM2 4.5l6 4.5 6-4.5v-.2H2z"/></symbol>
    <symbol id="i-globe" viewBox="0 0 16 16"><path d="M8 1a7 7 0 100 14A7 7 0 008 1zm0 1.8a5.2 5.2 0 013.8 1.6H9.5L8 6 6.5 7.5 8 9v3.2H6.8V10L4.2 7.4 3 8.2A5.2 5.2 0 018 2.8z"/></symbol>
  </defs>
</svg>

<!-- Letterhead -->
<section class="piece letterhead">
  <div class="wordmark">Renwick Digital</div>
  <p class="letter-greeting">Dear Ms. Harlow,</p>
  <div class="letter-body">
    <p>Thank you for meeting with our team last week to talk about the new brand rollout. We have gathered the notes from that session and shaped them into a clear plan for the months ahead, with each step set out in order.</p>
    <p>The first phase covers printed pieces such as cards, letterheads and envelopes. The second phase moves the same look onto the website, email signatures and social pages so that every point of contact feels the same.</p>
    <p>We will share first drafts within two weeks and gather your comments in a single round. Final files will follow soon after, along with a short guide that explains colours, type and spacing for anyone on your staff.</p>
    <p>Please let us know if any dates need to shift. We look forward to working with you on this project.</p>
  </div>
  <p class="letter-closing">Sincerely,</p>
  <div class="letter-signature" role="img" aria-label="Handwritten signature of Mara Quinlan"></div>
  <footer class="letter-footer">
    412 Larkspur Road, Juneau, Alaska 99801<br>
    <svg class="icon"><use href="#i-phone"/></svg> 555 210 4417
    <svg class="icon"><use href="#i-mobile"/></svg> 555 318 6620
    <svg class="icon"><use href="#i-fax"/></svg> 555 742 0395
    <svg class="icon"><use href="#i-mail"/></svg> hello@renwickdigital.example
    <svg class="icon"><use href="#i-globe"/></svg> www.renwickdigital.example
  </footer>
</section>

<!-- Presentation folder -->
<section class="piece folder">
  <span class="folder-spine" style="left:4px"></span>
  <span class="folder-spine" style="left:9px"></span>
  <span class="folder-spine" style="left:14px"></span>
  <div class="wordmark on-blue">Renwick<small>Digital</small></div>
</section>

<!-- Business card front -->
<section class="piece card-front">
  <div class="wordmark">Renwick Digital</div>
  <p class="card-url">www.renwickdigital.example</p>
</section>

<!-- Business card back, small -->
<section class="piece card-back small">
  <span class="white-side"></span>
  <span class="logo-field"></span>
  <div class="wordmark">Renwick<br>Digital</div>
  <div class="card-details">
    <p class="card-name">MARA QUINLAN</p>
    <p class="card-role">CEO/FOUNDER</p>
    <p class="contact">412 Larkspur Road<br>Juneau, Alaska 99801</p>
    <p class="contact">555 210 4417<svg class="icon"><use href="#i-phone"/></svg></p>
    <p class="contact">555 318 6620<svg class="icon"><use href="#i-mobile"/></svg></p>
    <p class="contact">555 742 0395<svg class="icon"><use href="#i-fax"/></svg></p>
    <p class="contact">hello@renwickdigital.example<svg class="icon"><use href="#i-mail"/></svg></p>
    <p class="contact">www.renwickdigital.example<svg class="icon"><use href="#i-globe"/></svg></p>
  </div>
</section>

<!-- Business card back, large -->
<section class="piece card-back large">
  <span class="white-side"></span>
  <span class="logo-field"></span>
  <div class="wordmark">Renwick<br>Digital</div>
  <div class="card-details">
    <p class="card-name">MARA QUINLAN</p>
    <p class="card-role">CEO/FOUNDER</p>
    <p class="contact address">412 Larkspur Road<br>Juneau, Alaska 99801</p>
    <p class="contact">555 210 4417<svg class="icon"><use href="#i-phone"/></svg></p>
    <p class="contact">555 318 6620<svg class="icon"><use href="#i-mobile"/></svg></p>
    <p class="contact">555 742 0395<svg class="icon"><use href="#i-fax"/></svg></p>
    <p class="contact">hello@renwickdigital.example<svg class="icon"><use href="#i-mail"/></svg></p>
    <p class="contact">www.renwickdigital.example<svg class="icon"><use href="#i-globe"/></svg></p>
  </div>
</section>

<!-- Envelope front -->
<section class="piece envelope-front">
  <div class="wordmark">Renwick Digital</div>
  <p class="envelope-address">412 Larkspur Road<br>Juneau, Alaska 99801</p>
  <span class="envelope-band"></span>
</section>

<!-- Envelope back -->
<section class="piece envelope-back">
  <svg class="envelope-flap" viewBox="0 0 386 56" aria-hidden="true">
    <path d="M0 0H386V8C380 14 378 28 372 40C368 50 362 54 352 54H34C24 54 18 50 14 40C8 28 6 14 0 8Z" fill="var(--brand-blue)"/>
  </svg>
  <div class="wordmark on-blue">Renwick Digital</div>
</section>

</body>
</html>
```